Retail Jewelry Business Card Design Project

We are in need of a new business card design for a retail jewelry store. This store is in the business of fine jewelry including but not specific to bridal jewelry, diamonds, designer jewelry and watches.

This store has been in business for 20 years but continues to strive for a modern professional appeal. The main colors use for this business are a royal blue, white and silver.

Target Market(s)

Target market is ages 18-50

Industry/Entity Type

Jewelry

Requirements
Must have
• Sales Person Name
Sales Person Email Address

Store Address
Store Phone
Website

Standard business card size. No odd shapes or sizes.
Nice to have
• Overall modern feel for card.

We have thought that a design with a nice feature of the logo on the back of the card would be nice but open to ideas.
Should not have
• No specific images of jewelry should be used.

```html
<!DOCTYPE html>
<html lang="en">
<head>
<meta charset="utf-8">
<title>Marlow Reed Fine Jewelry – Business Cards</title>
<link rel="stylesheet" href="https://fonts.googleapis.com/css2?family=Arimo:wght@400&family=Cinzel:wght@600&family=Libre+Baskerville:ital,wght@1,700&display=swap">
<style>
  :root {
    --royal-blue: #2e3192;
    --card-white: #ffffff;
    --stage: #ecebe8;
    --ink-grey: #4a4a4a;
    --edge: #d8d8dc;
  }
  * { box-sizing: border-box; margin: 0; padding: 0; }
  html, body {
    width: 1200px; height: 804px; overflow: hidden;
    background: var(--stage);
  }
  .stage { position: relative; width: 1200px; height: 804px; }

  .card {
    position: absolute;
    width: 540px; height: 309px;
    background: var(--card-white);
    border: 1px solid var(--edge);
    box-shadow: 0 6px 18px rgba(0,0,0,0.12);
    overflow: hidden;
  }
  .card--back { left: 40px; top: 110px; display: flex; }
  .card--front { left: 620px; top: 385px; }

  .wordmark {
    font-family: "Cinzel", serif;
    font-weight: 600;
    color: var(--royal-blue);
    text-align: center;
    line-height: 1.15;
  }

  /* back card */
  .back-brand {
    width: 228px; height: 100%;
    display: flex; align-items: center; justify-content: center;
  }
  .back-brand .wordmark { font-size: 25px; }
  .back-contact {
    flex: 1;
    background: var(--royal-blue);
    color: var(--card-white);
    padding: 34px 26px 0 30px;
    font-family: "Arimo", sans-serif;
  }
  .contact-name {
    font-family: "Libre Baskerville", serif;
    font-style: italic; font-weight: 700;
    font-size: 15px;
    margin-bottom: 18px;
  }
  .contact-list { list-style: none; font-size: 14px; line-height: 1.55; }
  .contact-list li { display: flex; align-items: center; gap: 8px; }
  .contact-list svg { width: 12px; height: 12px; flex: none; }
  .contact-address { margin-top: 22px; font-size: 14px; line-height: 1.45; }

  /* front card */
  .front-layout {
    height: 100%;
    display: flex; flex-direction: column;
    align-items: center; justify-content: center;
    gap: 50px;
  }
  .front-layout .wordmark { font-size: 44px; }
  .front-url {
    font-family: "Arimo", sans-serif;
    font-size: 16px;
    letter-spacing: 2px;
    color: var(--ink-grey);
  }
</style>
</head>
<body>
<main class="stage">

  <section class="card card--back" aria-label="Card back">
    <div class="back-brand">
      <p class="wordmark">Marlow Reed<br>Fine Jewelry</p>
    </div>
    <div class="back-contact">
      <p class="contact-name">Marlow Reed Ashford</p>
      <ul class="contact-list">
        <li>
          <svg viewBox="0 0 12 12" aria-hidden="true"><circle cx="6" cy="6" r="5.4" fill="none" stroke="#fff" stroke-width="1"/><path d="M4 3.2l1 1.4-.6.7c.4.9 1 1.5 1.9 1.9l.7-.6 1.4 1-.6 1c-2.4-.3-4.1-2-4.4-4.4z" fill="#fff"/></svg>
          555-013-2468
        </li>
        <li>
          <svg viewBox="0 0 12 12" aria-hidden="true"><circle cx="6" cy="6" r="5.4" fill="none" stroke="#fff" stroke-width="1"/><rect x="3" y="4" width="6" height="4" fill="none" stroke="#fff" stroke-width=".9"/><path d="M3 4l3 2.2L9 4" fill="none" stroke="#fff" stroke-width=".9"/></svg>
          marlow@marlowreedjewelry.com
        </li>
        <li>
          <svg viewBox="0 0 12 12" aria-hidden="true"><circle cx="6" cy="6" r="5.4" fill="none" stroke="#fff" stroke-width="1"/><ellipse cx="6" cy="6" rx="1.8" ry="4" fill="none" stroke="#fff" stroke-width=".8"/><path d="M2 6h8" stroke="#fff" stroke-width=".8"/></svg>
          www.marlowreedjewelry.com
        </li>
      </ul>
      <p class="contact-address">2280 Linden Avenue<br>Bayview, FL 32999</p>
    </div>
  </section>

  <section class="card card--front" aria-label="Card front">
    <div class="front-layout">
      <p class="wordmark">Marlow Reed<br>Fine Jewelry</p>
      <p class="front-url">www.marlowreedjewelry.com</p>
    </div>
  </section>

</main>
</body>
</html>
```